Lawn sign for construction company

Would like this to be a very clean and high end design for luxury homes. We need a yard sign designed that includes the company logo, website, phone number and major service offerings (residential and commercial renovations and maintenance)
The company website is brackwellbuilders.com all other contact info is in the attachments
Target Market(s)
Luxury home owners and business owners
Industry/Entity Type
Construction/Home Improvement
Font styles to use
Other font styles liked:
- See company logo and other graphics included for title text fonts. All other fonts can be standard sans serif.
Colors
0054AA
0677BA
7BADD7
CADEEF
E8F1F8
Requirements
Must have
- Clean, easy to read design, would like 2 sided sign. A main sign side and back side which states “free estimates, and includes the website and phone number. Must also match the color scheme of the provided logo and other company images. Dark Navy blue primary color, gray secondary color, and orange as an accent color.
Nice to have
- 2nd sign side very simple design
Should not have
- Too many graphics limit to 1-3 colors

```html
<!DOCTYPE html>
<html lang="en">
<head>
<meta charset="utf-8">
<title>Brackwell Builders – Lawn Sign</title>
<link href="https://fonts.googleapis.com/css2?family=Big+Shoulders+Stencil+Display:wght@800&family=Montserrat:wght@600;700&display=swap" rel="stylesheet">
<style>
  :root {
    --backdrop: #b4b4b4;
    --sign: #dadada;
    --navy: #0d1173;
    --navy-deep: #050a63;
    --orange: #e8780c;
    --gray: #6a6a6a;
    --stencil: "Big Shoulders Stencil Display", sans-serif;
    --sans: "Montserrat", sans-serif;
  }
  * { box-sizing: border-box; margin: 0; padding: 0; }
  html, body { width: 1200px; height: 1200px; overflow: hidden; }
  body { background: var(--backdrop); position: relative; }

  .sign {
    position: absolute;
    left: 219px;
    width: 720px;
    height: 480px;
    background: var(--sign);
  }
  .sign--front { top: 71px; }
  .sign--back { top: 609px; }

  .sign__frame {
    position: absolute;
    inset: 14px 14px;
    border: 1.5px solid var(--navy-deep);
  }

  .brand {
    position: absolute;
    left: 0; right: 0;
    top: 22px;
    height: 256px;
    display: flex;
    align-items: center;
    justify-content: center;
    gap: 16px;
  }
  .brand__mark {
    width: 26px; height: 26px;
    background: var(--navy);
  }
  .brand__name {
    font-family: var(--stencil);
    font-weight: 800;
    font-size: 62px;
    letter-spacing: 1px;
    color: var(--orange);
    line-height: 1;
  }

  .headline {
    position: absolute;
    left: 0; right: 0;
    top: 284px;
    text-align: center;
    font-family: var(--stencil);
    font-weight: 800;
    font-size: 78px;
    line-height: 1;
    color: var(--navy);
    letter-spacing: 1px;
  }

  .phone {
    position: absolute;
    left: 0; right: 0;
    top: 356px;
    display: flex;
    justify-content: center;
    align-items: center;
    gap: 6px;
    font-family: var(--sans);
    font-weight: 700;
    font-size: 50px;
    line-height: 1;
    color: var(--gray);
  }
  .phone__icon { width: 42px; height: 42px; }

  .web-pill {
    position: absolute;
    left: 112px;
    width: 494px;
    top: 412px;
    height: 40px;
    background: var(--orange);
    border-radius: 9px;
    display: flex;
    align-items: center;
    justify-content: center;
    font-family: var(--sans);
    font-weight: 600;
    font-size: 30px;
    color: var(--navy-deep);
  }

  .services {
    position: absolute;
    left: 0; right: 0;
    top: 328px;
    text-align: center;
    font-family: var(--stencil);
    font-weight: 800;
    font-size: 31px;
    line-height: 34px;
    color: var(--gray);
  }
  .services__dot {
    display: inline-block;
    width: 12px; height: 12px;
    background: var(--orange);
    margin: 0 6px;
    vertical-align: 4px;
  }

  .web-band {
    position: absolute;
    left: 14px; right: 14px;
    top: 402px;
    height: 66px;
    background: var(--navy-deep);
    display: flex;
    align-items: center;
    justify-content: center;
    font-family: var(--stencil);
    font-weight: 800;
    font-size: 46px;
    color: var(--orange);
    letter-spacing: 1px;
  }
</style>
</head>
<body>

<section class="sign sign--front">
  <div class="sign__frame"></div>
  <div class="brand">
    <span class="brand__mark"></span>
    <span class="brand__name">BRACKWELL BUILDERS</span>
  </div>
  <h1 class="headline">FREE ESTIMATES</h1>
  <div class="phone">
    <svg class="phone__icon" viewBox="0 0 48 48" aria-hidden="true">
      <path fill="#e8780c" d="M13 6c2 0 3 1 4 3l3 7c1 2 0 3-1 4l-3 3c2 5 6 9 11 11l3-3c1-1 2-2 4-1l7 3c2 1 3 2 3 4 0 5-4 9-9 9C18 46 2 30 2 12 2 7 7 6 13 6z"/>
      <path fill="none" stroke="#e8780c" stroke-width="3" stroke-linecap="round" d="M27 13a9 9 0 0 1 8 8M28 6a16 16 0 0 1 14 14M30 0a22 22 0 0 1 18 18"/>
    </svg>
    <span>800-555-0142</span>
  </div>
  <div class="web-pill">www.brackwellbuilders.com</div>
</section>

<section class="sign sign--back">
  <div class="sign__frame"></div>
  <div class="brand">
    <span class="brand__mark"></span>
    <span class="brand__name">BRACKWELL BUILDERS</span>
  </div>
  <p class="services">
    RESIDENTIAL RENOVATIONS<span class="services__dot"></span>COMMERCIAL<br>
    RENOVATIONS<span class="services__dot"></span>MAINTENANCE
  </p>
  <div class="web-band">www.brackwellbuilders.com</div>
</section>

</body>
</html>
```